Detail Shop Business card design

i need a business card design for my new detailing company called 'Brisk's Polish Works'. i want an all black and white design . simple, direct and to the point. i want the designer to choose a fitting font to match the logothe front should have logo, address, phone and email and the back side should have a slogan and text indicating that we offer services on anything including cars, trucks, motorcycles and RVs. slogan will read "we take pride in your ride"
maybe also very small on the back side the IG icon with Brisks_Polish_Works

phone 208.417.6352
address 3847 E Larkin Ave
Spokane WA 99214
email: BrisksPolish@mailvexo.com

Target Market(s)

all ages , auto enthusiasts

Industry/Entity Type

Automotive

Contact Information for Business Card

the front should have logo, address, phone and email and the back side should have a slogan and text indicating that we offer services on anything including cars, trucks, motorcycles and RVs. slogan will read "we take pride in your ride"

phone 208.417.6352
address 3847 E Larkin Ave
Spokane WA 99214

Colors
000000
ffffff

Requirements
Must have
• bold font and very simple design with good spacing
Nice to have
• anything creative from the designer indicating we service any types of vehicles
Should not have
• any colors ,

```html
<!DOCTYPE html>
<html lang="en">
<head>
<meta charset="utf-8">
<title>Brisk's Polish Works – Business Card</title>
<link rel="stylesheet" href="https://fonts.googleapis.com/css2?family=Roboto:wght@400;500&family=Roboto+Condensed:wght@400;700&display=swap">
<style>
  :root {
    --ink: #111111;
    --muted: #555555;
    --paper: #f4f4f4;
    --stage: #e2e2e2;
    --shade-dark: #1a1a1a;
    --shade-light: #8a8a8a;
  }
  * { box-sizing: border-box; margin: 0; padding: 0; }
  html, body { width: 1200px; height: 960px; overflow: hidden; }
  body { background: var(--stage); position: relative; font-family: "Roboto", Arial, sans-serif; color: var(--ink); }

  .card {
    position: absolute;
    width: 598px;
    height: 342px;
    background: var(--paper);
    box-shadow: 0 2px 6px rgba(0,0,0,0.25);
  }
  .card--front { left: 315px; top: 113px; }
  .card--back { left: 311px; top: 472px; width: 600px; }

  .hero-art {
    position: absolute;
    left: 330px; top: 27px;
    width: 256px; height: 92px;
    background: linear-gradient(180deg, var(--shade-light) 0%, var(--shade-dark) 70%, var(--ink) 100%);
    border-radius: 40px 40px 6px 6px;
  }

  .person { position: absolute; left: 25px; top: 146px; }
  .person__name { font-family: "Roboto Condensed", Arial Narrow, sans-serif; font-weight: 700; font-size: 21px; letter-spacing: 0.3px; line-height: 1; }
  .person__role { font-family: "Roboto Condensed", Arial Narrow, sans-serif; font-weight: 700; font-size: 15px; color: var(--muted); margin-top: 5px; }

  .address { position: absolute; left: 25px; top: 200px; font-size: 14px; line-height: 19px; color: #333; }

  .contacts { position: absolute; left: 25px; top: 246px; list-style: none; font-size: 14px; line-height: 19px; color: #333; }
  .contacts li { display: flex; align-items: center; gap: 9px; }
  .contacts svg { width: 13px; height: 13px; fill: var(--ink); flex: none; }

  .brand {
    position: absolute; left: 0; right: 0; top: 100px;
    display: flex; flex-direction: column; align-items: center; gap: 14px;
  }
  .brand__dot { width: 86px; height: 86px; border-radius: 50%; background: var(--ink); }
  .brand__name { font-family: "Roboto Condensed", Arial Narrow, sans-serif; font-weight: 700; font-size: 30px; color: var(--ink); letter-spacing: 0.5px; }

  .tagline { position: absolute; left: 0; right: 0; top: 272px; text-align: center; }
  .tagline__slogan {
    display: inline-block;
    font-family: "Roboto Condensed", Arial Narrow, sans-serif; font-weight: 700;
    font-size: 18px; letter-spacing: 0.4px;
    padding: 0 38px 3px;
    border-bottom: 1.5px solid var(--ink);
  }
  .tagline__services { font-family: "Roboto Condensed", Arial Narrow, sans-serif; font-size: 13.5px; margin-top: 3px; }
</style>
</head>
<body>

<section class="card card--front">
  <div class="hero-art" role="img" aria-label="Black and white illustration of a classic hot rod car"></div>

  <div class="person">
    <p class="person__name">DALE BRISKER</p>
    <p class="person__role">CEO/FOUNDER</p>
  </div>

  <p class="address">3847 E Larkin Ave<br>Spokane WA 99214</p>

  <ul class="contacts">
    <li><svg viewBox="0 0 24 24"><path d="M6.6 10.8a15.1 15.1 0 0 0 6.6 6.6l2.2-2.2a1 1 0 0 1 1-.25 11.4 11.4 0 0 0 3.6.57 1 1 0 0 1 1 1V20a1 1 0 0 1-1 1A17 17 0 0 1 3 4a1 1 0 0 1 1-1h3.5a1 1 0 0 1 1 1c0 1.25.2 2.45.57 3.57a1 1 0 0 1-.25 1z"/></svg>208.417.6352</li>
    <li><svg viewBox="0 0 24 24"><path d="M7 1h10a2 2 0 0 1 2 2v18a2 2 0 0 1-2 2H7a2 2 0 0 1-2-2V3a2 2 0 0 1 2-2zm0 3v14h10V4zm5 15.5a1.2 1.2 0 1 0 0 2.4 1.2 1.2 0 0 0 0-2.4z"/></svg>208 553 7180</li>
    <li><svg viewBox="0 0 24 24"><path d="M2 5h20v14H2zm2 2v.5l8 5 8-5V7zm0 2.8V17h16V9.8l-8 5z"/></svg>BrisksPolish@mailvexo.com</li>
    <li><svg viewBox="0 0 24 24"><path d="M12 2a10 10 0 1 0 0 20 10 10 0 0 0 0-20zm-1 17.9A8 8 0 0 1 4.2 10.8L9 15.6v1a2 2 0 0 0 2 2zm6.9-2.5A2 2 0 0 0 16 16h-1v-3a1 1 0 0 0-1-1H8v-2h2a1 1 0 0 0 1-1V7h2a2 2 0 0 0 2-2v-.4a8 8 0 0 1 2.9 12.8z"/></svg>www.briskspolishworks.com</li>
  </ul>
</section>

<section class="card card--back">
  <div class="brand">
    <span class="brand__dot"></span>
    <p class="brand__name">Brisk's Polish Works</p>
  </div>

  <div class="tagline">
    <p class="tagline__slogan">WE TAKE PRIDE IN YOUR RIDE</p>
    <p class="tagline__services">we offer services on anything including cars, trucks, motorcycles &amp; RVs</p>
  </div>
</section>

</body>
</html>
```